Simple Logo Design for Semi-Clear Plastic Frosted Card stock

Create a business card on frosted plastic. compliment existing logo elements with a tree trunk, roots, or seed at the lower half and the full logo both on the front.

Contact information will go on a solid portion of the back of this design since this card stock is semi-transparent.

It is important to consider this plastic card stock medium in your design. I found helpful tips and guides listed at vellaprint-sample.net: be careful to understand ink printed on plastic cards cannot have too much of a consistent print area or risks peeling and fine lines can easily scratch off.
Updates

2" x 3.5" 20PT Clear Plastic Business cards with Round corners Please get info or templates here: https://www.vellaprint-sample.net/product-detail/2-x-35-20pt-clear-plastic-business-cards-with-round-corners

Target Market(s)

Not for profit- religion

Industry/Entity Type

Business

Must include complementary elements to the existing logo

Font styles to use
Decorative

Colors
000000

Requirements
Must have
• Elements of community, nature and oneness. Such as: seed, roots, tree trunk, etc.
• Three lines of space on the back for Name, Title, Phone Number.
Nice to have
• I like a light use of decorative elements
Should not have
• No eyes, from faces or animals.

```html
<!DOCTYPE html>
<html lang="en">
<head>
<meta charset="utf-8">
<title>Steadfast Grove – Business Card</title>
<link href="https://fonts.googleapis.com/css2?family=Libre+Baskerville:wght@700&family=Roboto:wght@300;400&display=swap" rel="stylesheet">
<style>
  :root {
    --backdrop: #c9c9c9;
    --frost: #e6e6e4;
    --clear: rgba(235, 236, 236, 0.55);
    --charcoal: #333335;
    --teal: #1f5f59;
    --leaf: #3f9a3a;
    --ink-light: #f1f1f1;
    --ink-soft: #d6d6d6;
  }
  * { margin: 0; padding: 0; box-sizing: border-box; }
  html, body {
    width: 1200px;
    height: 952px;
    overflow: hidden;
    background: var(--backdrop);
  }
  .card {
    position: absolute;
    left: 100px;
    top: 190px;
    width: 1000px;
    height: 571px;
    border-radius: 48px;
    overflow: hidden;
    background: var(--frost);
    box-shadow: 0 10px 30px rgba(0, 0, 0, 0.18);
  }
  .card-art {
    position: absolute;
    inset: 0;
    width: 1000px;
    height: 571px;
  }
  .brand {
    position: absolute;
    left: 540px;
    top: 120px;
    width: 380px;
    display: flex;
    align-items: center;
    justify-content: center;
    gap: 14px;
  }
  .brand-dot {
    width: 34px;
    height: 34px;
    border-radius: 50%;
    background: var(--leaf);
    flex: none;
  }
  .brand-name {
    font-family: "Roboto", sans-serif;
    font-weight: 400;
    font-size: 44px;
    letter-spacing: 1px;
    color: var(--teal);
    text-transform: uppercase;
    white-space: nowrap;
  }
  .contact {
    position: absolute;
    right: 70px;
    top: 270px;
    text-align: right;
    color: var(--ink-light);
  }
  .contact-name {
    font-family: "Libre Baskerville", serif;
    font-weight: 700;
    font-size: 38px;
    line-height: 1.1;
  }
  .contact-title {
    font-family: "Roboto", sans-serif;
    font-weight: 300;
    font-size: 30px;
    color: var(--ink-soft);
    margin-top: 4px;
  }
  .contact-phone {
    font-family: "Roboto", sans-serif;
    font-weight: 300;
    font-size: 30px;
    color: var(--ink-soft);
    margin-top: 44px;
    display: flex;
    align-items: center;
    justify-content: flex-end;
    gap: 14px;
  }
  .phone-icon { width: 30px; height: 30px; }
</style>
</head>
<body>
  <div class="card">
    <svg class="card-art" viewBox="0 0 1000 571" xmlns="http://www.w3.org/2000/svg">
      <defs>
        <linearGradient id="trunk-tones" x1="0" y1="0" x2="0" y2="1">
          <stop offset="0" stop-color="#3e3826"/>
          <stop offset="0.6" stop-color="#5a4028"/>
          <stop offset="1" stop-color="#3d4a22"/>
        </linearGradient>
      </defs>
      <!-- clear left edge -->
      <rect class="clear-edge" x="0" y="0" width="90" height="571" fill="var(--clear)"/>
      <!-- dark contact band -->
      <path class="contact-band" d="M420,250 L1000,250 L1000,571 L470,571 Q462,380 420,250 Z" fill="var(--charcoal)"/>
      <!-- tree trunk and roots area -->
      <path class="trunk-photo" role="img" aria-label="Photograph of an old tree trunk with spreading roots over grass"
            d="M90,0 L330,0 Q452,250 462,571 L90,571 Z" fill="url(#trunk-tones)"/>
      <!-- sweeping curves -->
      <path class="curve-teal" d="M330,0 Q452,250 462,571" fill="none" stroke="var(--teal)" stroke-width="10"/>
      <path class="curve-dark" d="M352,0 Q474,250 484,571" fill="none" stroke="var(--charcoal)" stroke-width="12"/>
    </svg>

    <div class="brand">
      <span class="brand-dot"></span>
      <span class="brand-name">Steadfast Grove</span>
    </div>

    <div class="contact">
      <div class="contact-name">Owen Harlow</div>
      <div class="contact-title">Director</div>
      <div class="contact-phone">
        <span>0491 555 318</span>
        <svg class="phone-icon" viewBox="0 0 24 24" xmlns="http://www.w3.org/2000/svg" aria-hidden="true">
          <path d="M3 9 Q12 3 21 9 L19 12 L16 11 L16 9 Q12 7.5 8 9 L8 11 L5 12 Z" fill="var(--ink-light)"/>
          <rect x="6" y="13" width="12" height="8" rx="1.5" fill="var(--ink-light)"/>
          <circle cx="12" cy="17" r="2" fill="var(--charcoal)"/>
        </svg>
      </div>
    </div>
  </div>
</body>
</html>
```